Poster for a Bicycle show/Expo

We need a poster for a Bicycle show/Expo and sustainable transport. Exhibitors will sell bikes, cycling clothing, accessories, etc. ...
This show is annual and the Poster is for the 2015 edition.

The style must be modern, dynamic, bright colors.

Your concept must be compatible in a landscape format. (We will ourselves adaptations of different formats.)
Width: 210 mm
Height: 297 mm
It's necessary for us to have the source file (vector) for make, later, the different format (flyers, website, ...)

Content of the Poster:
- 1 big picture (no clip art)
- Big title: « Foire du Rayon » (« Salon » or « Salon du » can be small and « Vélo » big.)
- Subtitle: « et de la mobilité douce »
- Date: « 8, 9 et 10 mai 2015 » or « 8-10 mai 2015 »
- Place: « Halle TRV - Gare de Lunel »
- Text line 1: « www.foire-du-rayon.ch - Entrée gratuite »
- Text line 2« Piste d’essais - Restauration sur place »
- Text line 3: « Ve 8 mai de 17h à 21h - Sa 9 mai de 10h à 20h - Di 10 mai de 10h à 18h »
- Please, leave a zone in the poster for sponsors logos
(The predominant information (most visible) are: « Foire du Rayon » and « 8, 9 et 10 mai 2015 or 8-10 mai 2015 »)

Content of the big picture:
- from a cheap stock, like PixKiosk.com
- a bicycle in action or a detail of a bicycle (or a accessory) (no race bike)
- a modern picture with bright colors.
- if a person is on the picture, we prefer a men
- not an aerial view with cyclists in a landscape.

Some examples of poster of shows - with typo-title worked

http://www.expobassinlutece.com/Temp/IMG/F_a9b3c2d4e5f60718293a4b5c6d7e8f9012345678901_200_296.png

http://qx4m.tornafoire.fr/Data/pvtorn_mer/block/F_7cc1bb9396aef1d5e69283647561f0076457c357c5ea6.pdf
(page 2 of this PDF)

http://salons.rivol-evenements.fr/images/rivol-evenements/foires-salons/phototheque/salon-auto-bourlac/salon-auto-bourlac2012-affiche.jpg

http://www.tirovel.net/blog/wp-content/uploads/2007/03/affiche-salon-du-livre.jpg

http://www.quaimarin-gens.com/wp-content/affiche-cannes-2007.jpg
Updates

Hello,

For information, for your next versions, please, add the text "Piste d'essais".

- Text line 1: « www.foire-du-rayon.ch - Entrée gratuite »
- Text line 2: « Piste d’essais - Restauration sur place »
- Text line 3: « Ve 8 mai de 17h à 21h - Sa 9 mai de 10h à 20h - Di 10 mai de 10h à 18h »

Thanks,
Rodolphe

```html
<!DOCTYPE html>
<html lang="fr">
<head>
<meta charset="utf-8">
<title>Foire du Rayon et de la mobilité douce 2015</title>
<link href="https://fonts.googleapis.com/css2?family=Arimo:wght@700&family=Montserrat:wght@300;400&display=swap" rel="stylesheet">
<style>
  :root {
    --purple: #a6508c;
    --orange: #f1852e;
    --blue: rgba(40, 176, 233, 0.93);
    --white: #ffffff;
    --photo-light: #e9e8e6;
    --photo-mid: #cfd3d6;
    --photo-blue: #3b8fd0;
  }
  html, body {
    margin: 0;
    padding: 0;
    width: 849px;
    height: 1200px;
    overflow: hidden;
    background: var(--white);
  }
  .poster {
    position: relative;
    width: 849px;
    height: 1200px;
    overflow: hidden;
    font-family: "Montserrat", sans-serif;
    font-weight: 300;
    color: var(--white);
  }
  .hero-photo {
    position: absolute;
    inset: 0;
    background:
      radial-gradient(ellipse 180px 260px at 440px 200px, rgba(59, 143, 208, 0.55), transparent 70%),
      radial-gradient(ellipse 420px 480px at 450px 300px, #f7f7f6, transparent 75%),
      radial-gradient(ellipse 200px 600px at 690px 520px, rgba(40, 130, 200, 0.35), transparent 70%),
      linear-gradient(180deg, var(--photo-light) 0%, var(--photo-mid) 60%, #bcc6cc 100%);
  }
  .band {
    position: absolute;
    left: 90px;
    box-sizing: border-box;
  }
  .subtitle {
    top: 488px;
    width: 547px;
    height: 43px;
    background: var(--purple);
    padding-left: 19px;
    font-size: 29px;
    line-height: 43px;
    font-weight: 400;
  }
  .date-place {
    top: 539px;
    width: 547px;
    height: 42px;
    background: var(--purple);
    padding-left: 19px;
    font-size: 19.5px;
    line-height: 42px;
    font-weight: 400;
  }
  .info {
    top: 588px;
    height: 82px;
    background: var(--orange);
    padding: 7px 0 0 19px;
    font-size: 19px;
    line-height: 22.5px;
    font-weight: 400;
  }
  .info p { margin: 0; }
  .info-practical { width: 270px; }
  .info-hours { left: 367px; width: 270px; padding-left: 18px; }
  .title-block {
    top: 677px;
    width: 547px;
    height: 458px;
    background: var(--blue);
  }
  .title {
    margin: 0;
    position: absolute;
    left: 60px;
    top: 14px;
    font-family: "Arimo", sans-serif;
    font-weight: 700;
    font-size: 150px;
    line-height: 132px;
    letter-spacing: -3px;
  }
  .title span { display: block; }
  .title .title-main { font-size: 158px; margin-top: 8px; }
  .sponsor-zone {
    position: absolute;
    left: 637px;
    top: 677px;
    width: 212px;
    height: 458px;
    background: var(--white);
  }
</style>
</head>
<body>
<main class="poster">
  <div class="hero-photo" role="img" aria-label="Détail flou d'un vélo blanc et bleu : selle et cadre en gros plan"></div>

  <div class="band subtitle">et de la mobilité douce</div>
  <div class="band date-place">8, 9 et 10 mai 2015 | Halle TRV - Gare de Lunel</div>

  <div class="band info info-practical">
    <p>www.foire-du-rayon.ch</p>
    <p>Entrée gratuite</p>
    <p>Restauration sur place</p>
  </div>
  <div class="band info info-hours">
    <p>Ve 8 mai de 17h à 21h</p>
    <p>Sa 9 mai de 10h à 20h</p>
    <p>Di 10 mai de 10h à 18h</p>
  </div>

  <div class="band title-block">
    <h1 class="title">
      <span>Foire</span>
      <span>du</span>
      <span class="title-main">Rayon</span>
    </h1>
  </div>

  <aside class="sponsor-zone" aria-label="Zone partenaires"></aside>
</main>
</body>
</html>
```